The Linen Loft Co

We need a business card design for our wardrobe company.
Please visit our website www.gentlelinenlofts.com to get an idea of who we are.

```html
<!DOCTYPE html>
<html lang="en">
<head>
<meta charset="UTF-8">
<title>The Linen Loft Co – Business Card</title>
<link rel="stylesheet" href="https://fonts.googleapis.com/css2?family=Roboto:wght@400;500;700&display=swap">
<style>
  :root {
    --stage: #d6d6d6;
    --card: #ffffff;
    --ink: #111111;
    --text: #444444;
    --muted: #a6a6a6;
    --tab: #000000;
    --icon: #ffffff;
  }
  * { margin: 0; padding: 0; box-sizing: border-box; }
  html, body {
    width: 1200px; height: 800px; overflow: hidden;
    background: var(--stage);
    font-family: "Roboto", Arial, sans-serif;
  }
  .stage { position: relative; width: 1200px; height: 800px; }
  .card {
    position: absolute; top: 131px; height: 538px;
    background: var(--card);
  }
  .card-front { left: 124px; width: 462px; }
  .card-back {
    left: 586px; width: 490px;
    box-shadow: -8px 0 18px rgba(0,0,0,0.18);
  }

  /* Front */
  .brand {
    position: absolute; left: 63px; top: 236px;
    display: flex; align-items: center; gap: 18px;
  }
  .brand-mark {
    width: 58px; height: 58px;
    border: 2px solid var(--ink);
  }
  .brand-text { color: var(--ink); font-weight: 500; }
  .brand-name { font-size: 17px; letter-spacing: 0.2px; }
  .brand-tagline { font-size: 15px; margin-top: 8px; padding-left: 20px; }

  /* Back */
  .detail {
    position: absolute; left: 0; height: 52px; width: 100%;
    display: flex; align-items: center;
  }
  .detail-tab { position: absolute; left: 0; top: 0; width: 84px; height: 52px; }
  .detail-text {
    position: absolute; left: 106px;
    font-size: 21px; color: var(--text); line-height: 29px;
  }
  .detail-name { top: 82px; }
  .detail-address { top: 170px; }
  .detail-phone { top: 249px; }
  .detail-email { top: 324px; }
  .detail-web { top: 398px; }

  .person-name {
    font-size: 34px; font-weight: 700; color: var(--ink);
    line-height: 36px; top: -6px;
  }
  .person-role {
    position: absolute; left: 106px; top: 34px;
    font-size: 22px; font-weight: 500; color: var(--muted);
  }
  .detail-address .detail-text { top: -6px; }
</style>
</head>
<body>
<main class="stage">

  <section class="card card-front" aria-label="Card front">
    <div class="brand">
      <div class="brand-mark"></div>
      <div class="brand-text">
        <div class="brand-name">THE LINEN LOFT CO</div>
        <div class="brand-tagline">Order on Every Shelf</div>
      </div>
    </div>
  </section>

  <section class="card card-back" aria-label="Card back">
    <svg width="0" height="0" style="position:absolute">
      <defs>
        <path id="tab-shape" d="M0,0 H66 C88,8 88,44 66,52 H0 Z"/>
      </defs>
    </svg>

    <div class="detail detail-name">
      <svg class="detail-tab" viewBox="0 0 84 52">
        <use href="#tab-shape" fill="var(--tab)"/>
        <circle cx="40" cy="20" r="6" fill="var(--icon)"/>
        <path d="M28,36 Q28,27 40,27 Q52,27 52,36 Z" fill="var(--icon)"/>
      </svg>
      <div class="detail-text person-name">Daniel Hartley</div>
      <div class="person-role">President</div>
    </div>

    <div class="detail detail-address">
      <svg class="detail-tab" viewBox="0 0 84 52">
        <use href="#tab-shape" fill="var(--tab)"/>
        <path d="M38,38 C31,29 30,26 30,22 A8,8 0 0 1 46,22 C46,26 45,29 38,38 Z" fill="var(--icon)"/>
        <circle cx="38" cy="22" r="3" fill="var(--tab)"/>
      </svg>
      <div class="detail-text">Arden Court, 42 Mill Lane,<br>London N4 7QS</div>
    </div>

    <div class="detail detail-phone">
      <svg class="detail-tab" viewBox="0 0 84 52">
        <use href="#tab-shape" fill="var(--tab)"/>
        <path d="M31,17 L35,16 L38,22 L35,24 Q37,30 42,33 L44,30 L50,33 L49,37 Q46,40 40,37 Q32,32 30,24 Q29,19 31,17 Z" fill="var(--icon)"/>
      </svg>
      <div class="detail-text">020 7946 0518</div>
    </div>

    <div class="detail detail-email">
      <svg class="detail-tab" viewBox="0 0 84 52">
        <use href="#tab-shape" fill="var(--tab)"/>
        <rect x="30" y="20" width="20" height="13" fill="var(--icon)"/>
        <path d="M30,20 L40,28 L50,20" fill="none" stroke="var(--tab)" stroke-width="1.5"/>
      </svg>
      <div class="detail-text">info@gentlelinenlofts.com</div>
    </div>

    <div class="detail detail-web">
      <svg class="detail-tab" viewBox="0 0 84 52">
        <use href="#tab-shape" fill="var(--tab)"/>
        <circle cx="39" cy="26" r="9" fill="var(--icon)"/>
        <path d="M34,21 Q38,22 37,26 Q35,28 33,27 Z M41,18 Q44,21 42,24 Q45,27 46,31 Q42,31 40,28 Z" fill="var(--tab)"/>
      </svg>
      <div class="detail-text">www.gentlelinenlofts.com</div>
    </div>
  </section>

</main>
</body>
</html>
```